Book cover for book about Climate Change

Looking for a clean, bold, and attractive cover for a mass-market paperback (5.5"x 8.5") about solving the climate change problem. Title is either "Where the Rivers Meet” or A Harbor Made of Glass” (your choice), subtitle is "A practical field guide to mending the weather — so that the young ones after us inherit steady seasons and open skies," author is Lorne Whitcombe. Thinking that it *might* feature an image of Earth (or a portion thereof) and its very thin layer of atmosphere -- but STRONGLY encourage other ideas too!

Requirements
Nice to have
• Keep it positive — NOT scary doom-and-gloom

```html
<!DOCTYPE html>
<html lang="en">
<head>
<meta charset="utf-8">
<title>A Harbor Made of Glass — Lorne Whitcombe</title>
<link rel="stylesheet" href="https://fonts.googleapis.com/css2?family=Oswald:wght@400;500;700&family=Open+Sans:ital,wdth,wght@0,75..100,300..800;1,75..100,300..800&display=swap">
<style>
  :root {
    --space: #050506;
    --cloud: #e9ecef;
    --land: #b9a27c;
    --ocean: #2f5f80;
    --forest: #3f6b4a;
    --haze: #8fb7dd;
    --atmosphere: #5ea3ff;
    --ink: #ffffff;
    --ink-soft: #eef1f4;
    --spine-w: 72px;
  }
  html, body {
    margin: 0;
    padding: 0;
    width: 873px;
    height: 1200px;
    overflow: hidden;
    background: var(--space);
  }
  .book {
    position: relative;
    width: 873px;
    height: 1200px;
    overflow: hidden;
    background: var(--space);
    font-family: "Oswald", "Arial Narrow", sans-serif;
    color: var(--ink);
  }

  /* Spine */
  .spine {
    position: absolute;
    left: 0;
    top: 0;
    width: var(--spine-w);
    height: 1200px;
    overflow: hidden;
    border-right: 1px solid rgba(255, 255, 255, 0.25);
  }
  .spine-art {
    position: absolute;
    inset: 0;
    width: 100%;
    height: 100%;
  }
  .spine-title {
    position: absolute;
    top: 30px;
    left: 10px;
    margin: 0;
    writing-mode: vertical-rl;
    font-family: "Oswald", sans-serif;
    font-weight: 700;
    font-size: 38px;
    line-height: 40px;
    letter-spacing: 1px;
    text-transform: uppercase;
    color: var(--ink);
    text-shadow: 0 1px 4px rgba(0, 0, 0, 0.5);
  }
  .spine-author {
    position: absolute;
    bottom: 40px;
    left: 0;
    width: var(--spine-w);
    margin: 0;
    text-align: center;
    font-family: "Oswald", sans-serif;
    font-weight: 400;
    font-size: 17px;
    line-height: 21px;
    text-transform: uppercase;
    color: var(--ink-soft);
  }
  .spine-author span { display: block; }

  /* Front cover */
  .front {
    position: absolute;
    left: var(--spine-w);
    top: 0;
    width: calc(873px - var(--spine-w));
    height: 1200px;
    overflow: hidden;
  }
  .earth-view {
    position: absolute;
    inset: 0;
    width: 100%;
    height: 100%;
  }
  .author {
    position: absolute;
    top: 40px;
    left: 70px;
    margin: 0;
    font-family: "Oswald", sans-serif;
    font-weight: 400;
    font-size: 40px;
    line-height: 56px;
    letter-spacing: 20px;
    text-transform: uppercase;
    color: var(--ink-soft);
    text-shadow: 0 1px 6px rgba(0, 0, 0, 0.55);
  }
  .author span { display: block; }
  .title {
    position: absolute;
    top: 36px;
    right: 34px;
    margin: 0;
    text-align: right;
    font-family: "Oswald", sans-serif;
    font-weight: 700;
    font-size: 150px;
    line-height: 150px;
    letter-spacing: -1px;
    text-transform: uppercase;
    color: var(--ink);
    text-shadow: 0 3px 10px rgba(0, 0, 0, 0.35);
  }
  .title span { display: block; }
  .subtitle {
    position: absolute;
    left: 64px;
    top: 960px;
    width: 680px;
    margin: 0;
    font-family: "Open Sans", "Arial Narrow", sans-serif;
    font-stretch: 75%;
    font-weight: 300;
    font-size: 38px;
    line-height: 46px;
    text-transform: uppercase;
    color: var(--ink);
  }
  .subtitle strong {
    font-weight: 700;
    font-style: italic;
    font-size: 46px;
  }
</style>
</head>
<body>
  <main class="book">
    <aside class="spine">
      <svg class="spine-art" viewBox="0 0 72 1200" preserveAspectRatio="none" role="img" aria-label="Continuation of the Earth view: green land and blue sea fading into black space">
        <defs>
          <linearGradient id="spine-surface" x1="0" y1="0" x2="0" y2="1">
            <stop offset="0" stop-color="var(--ocean)"/>
            <stop offset="0.3" stop-color="var(--forest)"/>
            <stop offset="0.55" stop-color="var(--haze)"/>
            <stop offset="0.72" stop-color="var(--ocean)"/>
            <stop offset="0.78" stop-color="var(--space)"/>
            <stop offset="1" stop-color="var(--space)"/>
          </linearGradient>
        </defs>
        <rect width="72" height="1200" fill="url(#spine-surface)"/>
      </svg>
      <p class="spine-title">A Harbor Made of Glass</p>
      <p class="spine-author"><span>L</span><span>W</span><span>H</span><span>T</span></p>
    </aside>

    <section class="front">
      <svg class="earth-view" viewBox="0 0 801 1200" role="img" aria-label="Satellite view of Earth with clouds over land and sea, its thin blue atmosphere curving across the horizon into black space">
        <defs>
          <linearGradient id="surface" x1="0" y1="0" x2="1" y2="1">
            <stop offset="0" stop-color="var(--ocean)"/>
            <stop offset="0.18" stop-color="var(--forest)"/>
            <stop offset="0.34" stop-color="var(--cloud)"/>
            <stop offset="0.52" stop-color="var(--land)"/>
            <stop offset="0.72" stop-color="var(--cloud)"/>
            <stop offset="1" stop-color="var(--haze)"/>
          </linearGradient>
          <linearGradient id="limb" x1="0" y1="0" x2="0" y2="1">
            <stop offset="0" stop-color="var(--atmosphere)" stop-opacity="0.9"/>
            <stop offset="1" stop-color="var(--atmosphere)" stop-opacity="0"/>
          </linearGradient>
        </defs>
        <rect width="801" height="1200" fill="var(--space)"/>
        <path class="planet" d="M0 0 H801 V690 Q470 750 0 880 Z" fill="url(#surface)"/>
        <path class="atmosphere-glow" d="M0 880 Q470 750 801 690 L801 712 Q470 774 0 906 Z" fill="url(#limb)"/>
        <path class="atmosphere-line" d="M0 880 Q470 750 801 690" fill="none" stroke="var(--atmosphere)" stroke-width="5"/>
      </svg>

      <p class="author"><span>Lorne</span><span>Whitcombe</span></p>

      <h1 class="title">
        <span>A</span>
        <span>Harbor</span>
        <span>Made of</span>
        <span>Glass</span>
      </h1>

      <p class="subtitle"><strong>A practical field guide</strong> to mending the weather — so that the young ones after us inherit steady seasons and open skies</p>
    </section>
  </main>
</body>
</html>
```